Suds Haven Laundromat Wordpress Design

We need a Wordpress website design for our laundromat, Suds Haven Atlanta, at www.sudshavenatlanta-example.com. We would like to have 6 pages: Home, About Us, Services, Locations, Reviews and Contact us. We will provide content for the text on each page. What we do: We are a full service laundromat that provides dry cleaning drop off, professional laundry services, wash dry fold and self service laundry to the local community. We would like to use the color scheme from our logo to convey a warm, safe, and bright business that caters to its diverse community.
Updates

I like the structure of this laundromat website: http://www.washtroveusa-example.com/ Using my logo and color scheme in the above referenced website is what. Am looking for. The photos attached to the project with the female model should be used as a primary focus and supplemented by actual photos of the equipment.

Target Market(s)

Our target market is a diverse group of people from Midtown Atlanta - LGBTQ community /Locals/Regulars that have been coming to laundromat for 30 years.

Industry/Entity Type

Laundromat

Coding

Coded - Design and coding required

Number of Pages Required

5+ page

Font styles to use
Sans Serif

Colors
0054AA
0677BA
7BADD7
CADEEF
E8F1F8

Requirements
Must have
• Feature this video on the main page: https://videohost-example.com/xq7Rm2bPz4k

```html
<!DOCTYPE html>
<html lang="en">
<head>
<meta charset="utf-8">
<title>Suds Haven Atlanta</title>
<link href="https://fonts.googleapis.com/css2?family=Oswald:wght@300;400;500;600&family=Mulish:wght@400;600&display=swap" rel="stylesheet">
<style>
:root{
  --blue:#0054aa;
  --blue-mid:#1a63ad;
  --accent:#1fa3e0;
  --nav:#1565b5;
  --nav-active:#1e8fd6;
  --navy:#0a2b52;
  --ink:#1b1b1b;
  --text:#333;
  --white:#fff;
}
*{margin:0;padding:0;box-sizing:border-box}
html,body{width:1200px;height:2910px;overflow:hidden;background:#fff}
body{position:relative;font-family:'Mulish',sans-serif;color:var(--text)}
.abs{position:absolute}
.heading{font-family:'Oswald',sans-serif;font-weight:500;color:var(--ink);text-transform:uppercase;line-height:1.12}
.btn{position:absolute;border:1.5px solid var(--blue);color:var(--blue);font-size:11px;font-weight:600;text-transform:uppercase;display:flex;align-items:center;justify-content:center;letter-spacing:.3px}

/* header */
.brand{left:130px;top:18px;font-family:'Oswald',sans-serif;font-weight:500;font-size:30px;color:var(--blue);text-transform:uppercase;line-height:1}
.brand small{display:block;font-family:'Mulish',sans-serif;font-size:9px;font-weight:600;letter-spacing:.5px;margin-top:4px}
.social{display:flex;gap:7px}
.social span{width:27px;height:27px;border-radius:3px;background:#4f5e6b;display:block}
.contact-top{left:900px;top:14px;font-size:11px;line-height:15px;color:#222}
.contact-top .icon{position:absolute;left:-34px;top:2px;width:26px;height:26px;border-radius:3px;background:var(--accent)}
.contact-top b{font-weight:600}
.contact-top span{font-size:10px;color:#555}
.nav{left:610px;top:60px;width:590px;height:35px;background:var(--nav);display:flex;font-family:'Oswald',sans-serif;font-size:11.5px;color:#fff;text-transform:uppercase}
.nav a{display:flex;align-items:center;padding:0 19px;color:#fff;text-decoration:none}
.nav a.active{background:var(--nav-active)}

/* hero */
.hero{left:0;top:77px;width:1200px;height:500px;background:#060606;overflow:hidden}
.hero-photo{position:absolute;left:0;top:0;width:860px;height:500px;background:linear-gradient(90deg,#c9cccd 0%,#9aa4ab 30%,#a1603a 42%,#2a6fb7 58%,#1e3f66 75%,#060606 100%)}
.hero-copy{left:716px;top:122px;color:#fff}
.hero-copy .kicker{font-size:19px}
.hero-copy h1{font-family:'Oswald',sans-serif;font-weight:500;font-size:38px;line-height:51px;margin-top:8px;text-transform:uppercase}
.hero-copy .years{font-size:19px;font-weight:600;margin-top:12px;text-transform:uppercase}
.hero-copy .years em{font-style:normal;color:var(--accent)}
.hero .btn{left:716px;top:329px;width:105px;height:37px;border-color:var(--accent);color:#fff}
.hero-rail{left:1134px;top:125px;width:1px;height:190px;background:#555}

/* welcome */
.welcome{left:130px;top:672px;width:460px}
.welcome .kicker{font-size:17px;color:#222}
.welcome h2{font-size:39px;margin-top:8px}
.welcome p{font-size:13.3px;line-height:20.6px;color:#333;margin-top:30px;width:458px}
.welcome-photo{left:627px;top:626px;width:442px;height:432px;border-radius:50%;background:linear-gradient(160deg,#b6cfd6 0%,#8c9599 45%,#6b7074 100%);border-left:9px solid var(--blue)}

/* services */
.services{left:0;top:1108px;width:1200px;height:570px;background:linear-gradient(180deg,#1a5fa6,#1b5ea7)}
.services-bg{position:absolute;inset:0;background:linear-gradient(90deg,rgba(20,70,140,.6),rgba(60,110,170,.25) 50%,rgba(20,70,140,.6))}
.section-title{text-align:center;width:1200px;left:0}
.section-title .kicker{font-size:17px;color:#fff}
.section-title h2{font-size:39px;color:#fff;margin-top:0}
.card{position:absolute;top:237px;width:300px;height:262px;background:#fff}
.card .ring{position:absolute;left:110px;top:-42px;width:80px;height:80px;border-radius:50%;border:2px solid var(--blue);background:#fff}
.card h3{position:absolute;left:20px;top:70px;font-family:'Oswald',sans-serif;font-weight:500;font-size:17px;color:#111;text-transform:uppercase}
.card h3 em{font-style:normal;color:var(--blue)}
.card p{position:absolute;left:20px;top:104px;width:262px;font-size:12px;line-height:18.6px;color:#444}
.card .btn{left:20px;top:196px;width:105px;height:37px}
.arrow{position:absolute;top:353px;width:46px;height:28px;border:1.5px solid #fff;border-radius:14px}

/* reviews */
.reviews h2{font-size:39px;text-align:center;width:1200px;left:0;top:1725px}
.timeline{left:350px;top:1810px;width:2px;height:548px;background:#7b8fa6}
.review{position:absolute;left:130px;width:950px;height:160px}
.review .avatar{position:absolute;left:0;top:0;width:157px;height:157px;border-radius:50%}
.review .dot{position:absolute;left:211px;top:67px;width:22px;height:22px;border-radius:50%;border:3px solid var(--blue);background:#fff}
.review .name{position:absolute;left:321px;top:5px;font-size:23px;color:var(--blue)}
.review .role{position:absolute;left:321px;top:36px;font-size:13px;color:#555}
.review .stars{position:absolute;left:320px;top:60px;color:#f6b31b;font-size:17px;letter-spacing:4px}
.review p{position:absolute;left:320px;top:91px;width:620px;font-size:13.3px;line-height:20px;color:#222}

/* footer */
.footer{left:0;top:2410px;width:1200px;height:500px;background:var(--navy)}
.footer-note{left:476px;top:2598px;width:560px;font-family:'Oswald',sans-serif;font-weight:300;font-size:21px;line-height:28px;color:#fff}
.footer-brand{left:130px;top:2688px;font-family:'Oswald',sans-serif;font-weight:500;font-size:38px;color:#fff;text-transform:uppercase;line-height:1}
.footer-brand small{display:block;font-family:'Mulish',sans-serif;font-size:10px;font-weight:600;letter-spacing:.5px;margin-top:4px}
.footer-nav{left:476px;top:2706px;display:flex;gap:16px;font-family:'Oswald',sans-serif;font-size:11.5px;color:#fff;text-transform:uppercase}
.footer-rule{left:835px;top:2714px;width:170px;height:1px;background:#3e5a7d}
.footer-social{left:1010px;top:2702px}
.footer-social span{background:#7d8a97}
.footer-contact{left:476px;top:2769px;display:flex;gap:16px;font-size:11.5px;color:#fff;line-height:18px}
.footer-contact div{display:flex;gap:5px}
.footer-contact svg{flex:none;margin-top:4px}
.footer-divider{left:476px;top:2822px;width:596px;height:1px;background:#2e4a6e}
.copyright{left:476px;top:2840px;font-size:11.5px;color:#fff}
.copyright em{font-style:normal;color:var(--accent)}
</style>
</head>
<body>

<!-- Header -->
<div class="abs brand">Suds Haven<small>A Full Service Laundromat</small></div>
<div class="abs social" style="left:784px;top:16px"><span></span><span></span></div>
<div class="abs contact-top"><i class="icon"></i><b>+1 404-555-0182</b><br><span>hello@sudshavenatlanta-example.com</span></div>

<!-- Hero -->
<section class="abs hero">
  <div class="hero-photo" role="img" aria-label="Photo of a woman with red curly hair in a blue dress sitting beside a row of front-loading washers"></div>
  <div class="abs hero-copy">
    <div class="kicker">Coin Laundry</div>
    <h1>Dry Cleaning &amp;<br>Professional Laundry</h1>
    <div class="years">In business over <em>45 Years</em></div>
  </div>
  <div class="btn">Read More</div>
  <div class="abs hero-rail"></div>
  <svg class="abs" style="left:1127px;top:330px" width="16" height="38" viewBox="0 0 16 38">
    <circle cx="8" cy="8" r="6.5" fill="none" stroke="#fff" stroke-width="1.5"/><path d="M5 9.5l3-3 3 3" fill="none" stroke="#fff" stroke-width="1.5"/>
    <circle cx="8" cy="29" r="6.5" fill="none" stroke="#1fa3e0" stroke-width="1.5"/><path d="M5 27.5l3 3 3-3" fill="none" stroke="#1fa3e0" stroke-width="1.5"/>
  </svg>
  <svg class="abs" style="left:0;top:400px" width="1200" height="100" viewBox="0 0 1200 100" preserveAspectRatio="none">
    <path d="M0 100 L0 80 C 300 110 520 -10 860 12 C 1000 20 1120 50 1200 80 L1200 100 Z" fill="#fff"/>
  </svg>
</section>

<!-- Nav -->
<nav class="abs nav">
  <a class="active">Home</a><a>About Us</a><a>Services</a><a>Locations</a><a>Reviews</a><a>Contact Us.</a>
</nav>

<!-- Welcome -->
<section class="abs welcome">
  <div class="kicker">Welcome To</div>
  <h2 class="heading">Suds Haven<br>Atlanta</h2>
  <p>Sed ut perspiciatis unde omnis iste natus error sit voluptatem accusantium doloremque laudantium, totam rem aperiam, eaque ipsa quae ab illo inventore veritatis et quasi architecto beatae vitae dicta sunt explicabo. Nemo enim ipsam voluptatem quia voluptas sit aspernatur aut odit aut fugit, sed quia consequuntur magni dolores eos qui ratione voluptatem sequi nesciunt.</p>
</section>
<div class="btn" style="left:130px;top:963px;width:105px;height:37px">Read More</div>
<div class="abs welcome-photo" role="img" aria-label="Photo of stainless steel washing machines inside the laundromat"></div>

<!-- Services -->
<section class="abs services">
  <div class="services-bg" role="img" aria-label="Faded blue-tinted photo of laundromat washers"></div>
  <svg class="abs" style="left:0;top:0" width="1200" height="90" viewBox="0 0 1200 90" preserveAspectRatio="none">
    <path d="M0 0 L1200 0 L1200 32 C 1000 85 720 100 430 18 C 300 -8 120 -4 0 20 Z" fill="#fff"/>
  </svg>
  <div class="abs section-title" style="top:98px">
    <div class="kicker">Special</div>
    <h2 class="heading">Our Services</h2>
  </div>
  <div class="card" style="left:130px"><div class="ring"></div>
    <h3>Dry Cleaning <em>Drop Off</em></h3>
    <p>Sed ut perspiciatis unde omnis iste natus error sit voluptatem accusantium doloremque laudantium, totam rem aperiam, eaque ipsa quae ab illo inventore...</p>
    <div class="btn">Read More</div></div>
  <div class="card" style="left:450px"><div class="ring"></div>
    <h3>Professional <em>Laundry Services</em></h3>
    <p>Sed ut perspiciatis unde omnis iste natus error sit voluptatem accusantium doloremque laudantium, totam rem aperiam, eaque ipsa quae ab illo inventore...</p>
    <div class="btn">Read More</div></div>
  <div class="card" style="left:770px"><div class="ring"></div>
    <h3>Wash <em>Dry Fold</em></h3>
    <p>Sed ut perspiciatis unde omnis iste natus error sit voluptatem accusantium doloremque laudantium, totam rem aperiam, eaque ipsa quae ab illo inventore...</p>
    <div class="btn">Read More</div></div>
  <div class="arrow" style="left:42px"><svg width="46" height="28" viewBox="0 0 46 28"><path d="M25 9l-5 5 5 5" fill="none" stroke="#fff" stroke-width="1.5"/></svg></div>
  <div class="arrow" style="left:1112px"><svg width="46" height="28" viewBox="0 0 46 28"><path d="M21 9l5 5-5 5" fill="none" stroke="#fff" stroke-width="1.5"/></svg></div>
</section>

<!-- Reviews -->
<section class="reviews">
  <h2 class="abs heading">Customer Review</h2>
  <div class="abs timeline"></div>
  <div class="review" style="top:1810px">
    <div class="avatar" role="img" aria-label="Portrait photo of a customer" style="background:linear-gradient(135deg,#d9d9d9,#9a9a9a)"></div>
    <div class="dot"></div>
    <div class="name">Marco Tellis</div><div class="role">Met Amuter</div>
    <div class="stars">★★★★★</div>
    <p>Sed ut perspiciatis unde omnis iste natus error sit voluptatem accusantium doloremque laudantium, totam rem aperiam, eaque ipsa quae ab illo inventore veritatis et quasi architecto beatae vitae dicta sunt explicabo.</p>
  </div>
  <div class="review" style="top:2005px">
    <div class="avatar" role="img" aria-label="Portrait photo of a customer" style="background:linear-gradient(135deg,#d8d0d8,#c59a7c)"></div>
    <div class="dot"></div>
    <div class="name">Sara Lindqvist</div><div class="role">Met Amuter</div>
    <div class="stars">★★★★★</div>
    <p>Sed ut perspiciatis unde omnis iste natus error sit voluptatem accusantium doloremque laudantium, totam rem aperiam, eaque ipsa quae ab illo inventore veritatis et quasi architecto beatae vitae dicta sunt explicabo.</p>
  </div>
  <div class="review" style="top:2200px">
    <div class="avatar" role="img" aria-label="Portrait photo of a customer" style="background:linear-gradient(135deg,#9fd3d6,#d9cdb8)"></div>
    <div class="dot"></div>
    <div class="name">Greta Olsen</div><div class="role">Met Amuter</div>
    <div class="stars">★★★★★</div>
    <p>Sed ut perspiciatis unde omnis iste natus error sit voluptatem accusantium doloremque laudantium, totam rem aperiam, eaque ipsa quae ab illo inventore veritatis et quasi architecto beatae vitae dicta sunt explicabo.</p>
  </div>
</section>

<!-- Footer -->
<footer class="abs footer">
  <svg class="abs" style="left:0;top:0" width="1200" height="80" viewBox="0 0 1200 80" preserveAspectRatio="none">
    <path d="M0 0 L1200 0 L985 0 C 900 40 760 78 520 60 C 330 46 150 50 0 20 Z" fill="#fff"/>
  </svg>
</footer>
<div class="abs footer-note">Located conveniently in Midtown next to Baker's Pantry in The Linden Mall Shopping Center.</div>
<div class="abs footer-brand">Suds Haven<small>A Full Service Laundromat</small></div>
<div class="abs footer-nav"><span>Home</span><span>About Us</span><span>Services</span><span>Locations</span><span>Reviews</span><span>Contact Us</span></div>
<div class="abs footer-rule"></div>
<div class="abs social footer-social"><span></span><span></span></div>
<div class="abs footer-contact">
  <div><svg width="8" height="11" viewBox="0 0 8 11"><path d="M4 0a4 4 0 0 0-4 4c0 3 4 7 4 7s4-4 4-7a4 4 0 0 0-4-4z" fill="#1fa3e0"/><circle cx="4" cy="4" r="1.4" fill="#0a2b52"/></svg><span>2210 Magnolia Ave NE Ste 108 Atlanta,<br>GA, US 30300</span></div>
  <div><svg width="10" height="10" viewBox="0 0 10 10"><path d="M2 0l2 2.5-1.2 1.3a6 6 0 0 0 3.4 3.4L7.5 6 10 8 8.5 10C4 10 0 6 0 1.5z" fill="#1fa3e0"/></svg><span>+1 404-555-0182</span></div>
  <div><svg width="11" height="8" viewBox="0 0 11 8"><rect width="11" height="8" fill="#1fa3e0"/><path d="M0 0l5.5 4.5L11 0" fill="none" stroke="#0a2b52"/></svg><span>hello@sudshavenatlanta-example.com</span></div>
</div>
<div class="abs footer-divider"></div>
<div class="abs copyright">Copyright © 2021 <em>Suds Haven Atlanta</em>. All Rights Reserved.</div>

</body>
</html>
```